Heron Loan Partners Business Card

We need a business card design for our mortgage servicing company. In addition to servicing the loans of homeowners, we help homeowners with purchasing their homes and any mortgage refinancing. We would like to see designs that use the colors in the logo attached below (gold-ish yellow and navy blue), and any other design you deem fit! The design should communicate a simpler life with smart mortgages provided by Heron.

```html
<!DOCTYPE html>
<html lang="en">
<head>
<meta charset="utf-8">
<title>Heron Loan Partners Business Card</title>
<link href="https://fonts.googleapis.com/css2?family=Arimo:wght@400;700&display=swap" rel="stylesheet">
<style>
  :root {
    --navy: #221e55;
    --gold: #e3b12c;
    --white: #ffffff;
    --backdrop: #e4e4e8;
    --ink-light: #f2f2f6;
  }
  * { box-sizing: border-box; margin: 0; padding: 0; }
  html, body { width: 1200px; height: 874px; overflow: hidden; }
  body {
    background: var(--backdrop);
    font-family: "Arimo", Arial, sans-serif;
    position: relative;
  }
  .card {
    position: absolute;
    left: 290px;
    width: 620px;
    height: 354px;
    border-radius: 22px;
    overflow: hidden;
    box-shadow: 0 6px 18px rgba(0,0,0,0.18);
  }
  .card-front { top: 58px; background: var(--navy); }
  .card-back { top: 462px; background: var(--navy); display: flex; }

  .front-brand {
    position: absolute;
    left: 0; right: 0; top: 112px;
    text-align: center;
    color: var(--gold);
    font-weight: 700;
  }
  .front-brand .brand-name { font-size: 64px; line-height: 1; letter-spacing: 0.5px; }
  .front-brand .brand-sub { font-size: 18px; letter-spacing: 4px; margin-top: 6px; }
  .tagline {
    position: absolute;
    left: 0; right: 0; top: 262px;
    text-align: center;
    color: var(--ink-light);
    font-size: 15px;
  }

  .back-logo-panel {
    width: 294px;
    background: var(--white);
    display: flex;
    flex-direction: column;
    align-items: center;
    justify-content: center;
    color: var(--gold);
    font-weight: 700;
  }
  .back-logo-panel .brand-name { font-size: 38px; line-height: 1; }
  .back-logo-panel .brand-sub { font-size: 11px; letter-spacing: 2.5px; margin-top: 4px; }
  .gold-rule { width: 7px; background: var(--gold); }
  .contact-panel {
    flex: 1;
    padding: 58px 0 0 34px;
    color: var(--white);
  }
  .person-name { color: var(--gold); font-weight: 700; font-size: 25px; }
  .person-role { font-size: 14px; margin-top: 2px; }
  .address { font-size: 15px; line-height: 1.3; margin-top: 22px; }
  .contact-list { list-style: none; margin-top: 14px; font-size: 15px; line-height: 1.35; }
  .contact-list li { display: flex; align-items: center; gap: 10px; }
  .contact-list svg { width: 12px; height: 12px; fill: var(--gold); flex: none; }
</style>
</head>
<body>
  <section class="card card-front">
    <div class="front-brand">
      <div class="brand-name">Heron</div>
      <div class="brand-sub">LOAN PARTNERS</div>
    </div>
    <p class="tagline">Simpler life with smart mortgages</p>
  </section>

  <section class="card card-back">
    <div class="back-logo-panel">
      <div class="brand-name">Heron</div>
      <div class="brand-sub">LOAN PARTNERS</div>
    </div>
    <div class="gold-rule"></div>
    <div class="contact-panel">
      <h1 class="person-name">Daniel Reeves</h1>
      <p class="person-role">President</p>
      <p class="address">4215 Willow Bend Road<br>Halifax, Canada 20318</p>
      <ul class="contact-list">
        <li><svg viewBox="0 0 12 12"><path d="M2 0h3l1 3-2 1a7 7 0 0 0 4 4l1-2 3 1v3a2 2 0 0 1-2 2A10 10 0 0 1 0 2a2 2 0 0 1 2-2z"/></svg>555-214-7789</li>
        <li><svg viewBox="0 0 12 12"><path d="M3 0h6a1 1 0 0 1 1 1v10a1 1 0 0 1-1 1H3a1 1 0 0 1-1-1V1a1 1 0 0 1 1-1zm0 1.5v8h6v-8z"/></svg>555-390-1462</li>
        <li><svg viewBox="0 0 12 12"><path d="M0 2h12v8H0zm1 1v.4l5 3.3 5-3.3V3z"/></svg>info@heronloanpartners.com</li>
        <li><svg viewBox="0 0 12 12"><circle cx="6" cy="6" r="6"/></svg>www.heronloanpartners.com</li>
      </ul>
    </div>
  </section>
</body>
</html>
```